Bramwell IT Services Business Card

Bramwell IT Services are a Perth based IT Services company. We would like to incorporate our company logo (attached) and stick with the blue that is in that design. I would like a clean look design that isn't too busy, yet creates a lasting image that is instantly recognisable in the recipients mind.

Target Market(s)

The target audience is small/medium business owners.

Industry/Entity Type

Business

Font styles to use
Serif
Sans Serif

Colors

Designer to choose colors to be used in the design.

Requirements
Must have
• The design should include:
Business name: Bramwell IT Services
Directors Name: Marcus Tenley
Phone Number: 0483 562 904
Email: support@bramwellit.com.au
Website: www.bramwellit.com.au

```html
<!DOCTYPE html>
<html lang="en">
<head>
<meta charset="utf-8">
<title>Bramwell IT Services – Business Card</title>
<link rel="stylesheet" href="https://fonts.googleapis.com/css2?family=Questrial&family=Open+Sans:wght@700&display=swap">
<style>
  :root {
    --canvas-bg: #d9dadc;
    --card-black: #0b0c0e;
    --card-edge: #1a1c20;
    --brand-blue: #1a86e0;
    --band-blue: #0a9be6;
    --deep-blue: #0f3b66;
    --text-light: #e9edf2;
    --text-muted: #c9ced6;
  }
  * { margin: 0; padding: 0; box-sizing: border-box; }
  html, body { width: 1200px; height: 900px; overflow: hidden; }
  body {
    background: var(--canvas-bg);
    font-family: "Questrial", "Century Gothic", sans-serif;
  }
  .sheet {
    width: 1200px; height: 900px;
    display: flex; flex-direction: column;
    align-items: center; justify-content: center;
    gap: 40px;
  }
  .card {
    position: relative;
    width: 700px; height: 400px;
    background: var(--card-black);
    overflow: hidden;
    box-shadow: 0 6px 18px rgba(0,0,0,0.25);
  }

  /* Back: centred company name */
  .card--back {
    display: flex; align-items: center; justify-content: center;
  }
  .wordmark {
    display: flex; align-items: center; gap: 14px;
    color: var(--brand-blue);
  }
  .wordmark__square {
    width: 22px; height: 22px; background: var(--brand-blue);
  }
  .wordmark__text { line-height: 1; }
  .wordmark__name {
    display: block; font-size: 44px; letter-spacing: 1px; text-transform: uppercase;
  }
  .wordmark__sub {
    display: block; font-size: 14px; letter-spacing: 6px; text-transform: uppercase;
    margin-top: 6px;
  }

  /* Front */
  .card__glow {
    position: absolute; left: -40px; top: -60px;
    width: 380px; height: 300px;
    background: radial-gradient(ellipse at 45% 55%, rgba(20,70,110,0.55) 0%, rgba(15,50,85,0.25) 45%, rgba(11,12,14,0) 75%);
  }
  .card--front .wordmark {
    position: absolute; right: 44px; top: 96px;
  }
  .card--front .wordmark__name { font-size: 38px; }
  .card--front .wordmark__sub { font-size: 12px; letter-spacing: 5px; text-align: right; }

  .name-band {
    position: absolute; left: 300px; right: 0; top: 178px; height: 52px;
    background: var(--band-blue);
    display: flex; align-items: center; padding-left: 26px;
  }
  .name-band__name {
    font-family: "Open Sans", Arial, sans-serif; font-weight: 700;
    font-size: 26px; color: #ffffff;
  }

  .contact {
    position: absolute; left: 40px; top: 246px;
    list-style: none;
  }
  .contact__row {
    display: flex; align-items: baseline; gap: 26px;
    font-size: 17px; color: var(--text-muted); line-height: 32px;
  }
  .contact__label {
    width: 12px; color: var(--band-blue);
    font-family: "Open Sans", Arial, sans-serif; font-weight: 700; font-size: 13px;
  }
</style>
</head>
<body>
<main class="sheet">
  <section class="card card--back" aria-label="Business card back">
    <div class="wordmark">
      <span class="wordmark__square"></span>
      <span class="wordmark__text">
        <span class="wordmark__name">Bramwell</span>
        <span class="wordmark__sub">IT Services</span>
      </span>
    </div>
  </section>

  <section class="card card--front" aria-label="Business card front">
    <div class="card__glow" role="img" aria-label="Faint brand emblem decoration"></div>
    <div class="wordmark">
      <span class="wordmark__text">
        <span class="wordmark__name">Bramwell</span>
        <span class="wordmark__sub">IT Services</span>
      </span>
    </div>
    <div class="name-band">
      <span class="name-band__name">Marcus Tenley</span>
    </div>
    <ul class="contact">
      <li class="contact__row"><span class="contact__label">P</span><span>0483 562 904</span></li>
      <li class="contact__row"><span class="contact__label">E</span><span>support@bramwellit.com.au</span></li>
      <li class="contact__row"><span class="contact__label">W</span><span>www.bramwellit.com.au</span></li>
    </ul>
  </section>
</main>
</body>
</html>
```